tinyTally Resource Book - 10 maths tasks to do outside

I need a 22 (11 pages back to back) page A6 sized book produced to standard for submission to professional printer. Needs to be as .pdf file showing guide lines and allowances for colour bleed. I have text already written and submitted as attachment in a Word file with margins set to A6 size. The theme of the materials is "Nature Play" so using lots of pictures from nature (Australia preferably) and showing lots of patterns in nature (rocks, leaves, flower petals etc). Some of the tasks refer to specific activities, such as "shadows" and "floating" so would be great to illustrate appropriately. The big emphasis is on learning outside the classroom, getting kids to engage actively with nature. I would like to see the pages as full colour - so not white background. The book itself will be spiral bound along the top edge so a margin of at least 1cm will be required at the top of each page (or the bottom of even numbered pages). Book will be printed on plastic laminated matte paper for outdoor use. Font size needs to be big enough to read. Fonts sizes, alignments and page numbers are all different at the moment and need to be standardised. One photo is included in a page as a sample if you can use it, otherwise disregard. Logo for Wattlebrook Numeracy Guild is also included to have as part of the acknowledgements at the back of the book.

Target Market(s)

Book is for early childhood and preschool teachers.

Industry/Entity Type

Education

Font styles to use
Sans Serif

Requirements
Must have
• Colour and appeal.
Nice to have
• Use of natural colours instead of bright catchy colours but that is your call.
Should not have
• American spelling

```html
<!DOCTYPE html>
<html lang="en-AU">
<head>
<meta charset="utf-8">
<title>tinyTally Resource Book – 9. Rolling</title>
<link href="https://fonts.googleapis.com/css2?family=Nunito:wght@900&family=Questrial&display=swap" rel="stylesheet">
<style>
  :root {
    --paper: #ffffff;
    --wood-light: #e9bf8c;
    --wood-mid: #dcaa72;
    --wood-dark: #cf9a62;
    --heading: #2b2f8f;
    --heading-edge: #ffffff;
    --body-text: #2f2a27;
    --bullet: #d2232a;
    --badge: #2b2f8f;
    --badge-text: #ffffff;
    --crop: #555555;
    --stone-tone: #8a6e55;
    --ball-tone: #3a86cf;
  }
  html, body {
    margin: 0;
    padding: 0;
    width: 892px;
    height: 1200px;
    overflow: hidden;
    background: var(--paper);
  }
  .page {
    position: relative;
    width: 892px;
    height: 1200px;
    font-family: "Questrial", "Century Gothic", sans-serif;
    color: var(--body-text);
  }
  .crop-marks {
    position: absolute;
    inset: 0;
  }
  .bleed-area {
    position: absolute;
    left: 54px;
    top: 56px;
    width: 784px;
    height: 1090px;
    background:
      repeating-linear-gradient(90deg, rgba(255,255,255,0.10) 0 3px, rgba(0,0,0,0) 3px 19px, rgba(150,90,40,0.06) 19px 23px, rgba(0,0,0,0) 23px 41px),
      linear-gradient(90deg, var(--wood-mid), var(--wood-light) 30%, var(--wood-mid) 60%, var(--wood-light) 85%, var(--wood-dark));
  }
  .section-title {
    position: absolute;
    left: 125px;
    margin: 0;
    font-family: "Nunito", "Gill Sans", sans-serif;
    font-weight: 900;
    color: var(--heading);
    line-height: 1;
    white-space: nowrap;
    text-shadow:
      -2px -2px 0 var(--heading-edge), 2px -2px 0 var(--heading-edge),
      -2px 2px 0 var(--heading-edge), 2px 2px 0 var(--heading-edge),
      0 -2px 0 var(--heading-edge), 0 2px 0 var(--heading-edge),
      -2px 0 0 var(--heading-edge), 2px 0 0 var(--heading-edge),
      3px 4px 4px rgba(0,0,0,0.35);
  }
  .task-title { top: 140px; font-size: 51px; }
  .sub-title { font-size: 43px; }
  .prompts-title { top: 354px; }
  .variations-title { top: 746px; }
  .ideas-title { top: 920px; }
  .point-list {
    position: absolute;
    left: 186px;
    width: 620px;
    margin: 0;
    padding: 0;
    list-style: none;
    font-size: 31px;
    line-height: 36.3px;
    white-space: nowrap;
    -webkit-text-stroke: 0.5px var(--body-text);
  }
  .point-list li {
    position: relative;
    padding-left: 32px;
  }
  .point-list li::before {
    content: "";
    position: absolute;
    left: 2px;
    top: 12px;
    width: 12px;
    height: 12px;
    background: var(--bullet);
    transform: rotate(45deg);
  }
  .steps-list { top: 198px; }
  .prompts-list { top: 408px; }
  .variations-list { top: 800px; }
  .ideas-list { top: 974px; }
  .photo {
    position: absolute;
  }
  .photo-stone {
    left: 466px;
    top: 936px;
    width: 74px;
    height: 128px;
    background: var(--stone-tone);
  }
  .photo-ball {
    left: 573px;
    top: 872px;
    width: 147px;
    height: 146px;
    background: var(--ball-tone);
  }
  .page-number {
    position: absolute;
    left: 696px;
    top: 1024px;
    width: 74px;
    height: 72px;
  }
  .page-number span {
    position: absolute;
    inset: 0;
    display: flex;
    align-items: center;
    justify-content: center;
    padding-top: 10px;
    color: var(--badge-text);
    font-size: 31px;
  }
</style>
</head>
<body>
<div class="page">
  <div class="bleed-area" role="img" aria-label="Light bamboo wood grain background"></div>

  <svg class="crop-marks" width="892" height="1200" viewBox="0 0 892 1200" aria-hidden="true">
    <g stroke="var(--crop)" stroke-width="0.8" fill="none">
      <line x1="53" y1="0" x2="53" y2="40"/>
      <line x1="0" y1="55" x2="38" y2="55"/>
      <line x1="74" y1="36" x2="74" y2="74"/><line x1="36" y1="74" x2="74" y2="74"/>
      <line x1="839" y1="0" x2="839" y2="40"/>
      <line x1="854" y1="55" x2="892" y2="55"/>
      <line x1="818" y1="36" x2="818" y2="74"/><line x1="818" y1="74" x2="856" y2="74"/>
      <line x1="53" y1="1160" x2="53" y2="1200"/>
      <line x1="0" y1="1145" x2="38" y2="1145"/>
      <line x1="74" y1="1126" x2="74" y2="1164"/><line x1="36" y1="1126" x2="74" y2="1126"/>
      <line x1="839" y1="1160" x2="839" y2="1200"/>
      <line x1="854" y1="1145" x2="892" y2="1145"/>
      <line x1="818" y1="1126" x2="818" y2="1164"/><line x1="818" y1="1126" x2="856" y2="1126"/>
    </g>
  </svg>

  <h1 class="section-title task-title">9. Rolling</h1>
  <ul class="point-list steps-list">
    <li>Get a collection of objects – stones,<br>balls, toys etc</li>
    <li>Roll them down a slope</li>
    <li>Record how far they go</li>
  </ul>

  <h2 class="section-title sub-title prompts-title">Prompting questions</h2>
  <ul class="point-list prompts-list">
    <li>Which one went the furthest?</li>
    <li>If we tested the same object again,<br>would it go the same distance as the<br>first time?</li>
    <li>Why do some go further than others?</li>
    <li>How can you make something go fur-<br>ther?</li>
    <li>How do objects roll – straight? wobbly?<br>etc</li>
  </ul>

  <h2 class="section-title sub-title variations-title">Variations</h2>
  <ul class="point-list variations-list">
    <li>Change angle of the slope</li>
    <li>Change surface we roll<br>on – dirt, grass, sand</li>
  </ul>

  <h2 class="section-title sub-title ideas-title">Big Ideas</h2>
  <ul class="point-list ideas-list">
    <li>Distance</li>
    <li>Slope, angle</li>
  </ul>

  <div class="photo photo-stone" role="img" aria-label="Photo of a smooth brown stone"></div>
  <div class="photo photo-ball" role="img" aria-label="Photo of a blue exercise ball"></div>

  <div class="page-number">
    <svg width="74" height="72" viewBox="0 0 74 72" aria-hidden="true">
      <polygon points="37,0 74,27 60,72 14,72 0,27" fill="var(--badge)"/>
    </svg>
    <span>19</span>
  </div>
</div>
</body>
</html>
```